Business Card and Letterhead for Pimlu - modern real estate business

I need a double sided business card design for Pimlu. Please see business card brief here https://files.trelvonadocs.com/sheet/r/7QzTmWbaXLJnoPEd-kRyUgFhHsstbvCe2qfoMxDa_pz/view?mode=shared

Please feel free to design the business cards however you feel best. I am happy to give some creative freedoms and then provide feedback from there.

Please then also create a letterhead to match the business card design

Colors

Designer to choose colors to be used in the design.

Requirements
Must have
• Must be a modern, elegant business card which looks very professional

```html
<!DOCTYPE html>
<html lang="en">
<head>
<meta charset="utf-8">
<title>Pimlu Letterhead</title>
<link href="https://fonts.googleapis.com/css2?family=Open+Sans:wght@400;700&display=swap" rel="stylesheet">
<style>
  :root {
    --backdrop: #a5b5ba;
    --paper: #ffffff;
    --brand-red: #e3131b;
    --ink: #3d3d3d;
    --ink-dark: #222222;
    --rule: #555555;
    --signature-tone: #e4e4e4;
  }
  * { margin: 0; padding: 0; box-sizing: border-box; }
  html, body {
    width: 1200px; height: 907px; overflow: hidden;
    background: var(--backdrop);
    font-family: "Open Sans", Arial, sans-serif;
  }
  .letterhead {
    position: absolute; left: 290px; top: 58px;
    width: 620px; height: 792px;
    background: var(--paper);
    box-shadow: 2px 3px 8px rgba(0,0,0,0.25);
  }
  .brand-name {
    position: absolute; left: 420px; top: 20px;
    font-size: 41px; font-weight: 700; letter-spacing: 1px;
    color: var(--brand-red); line-height: 1;
  }
  .letter-date {
    position: absolute; left: 68px; top: 220px;
    font-size: 10.5px; color: var(--ink);
  }
  .letter-body {
    position: absolute; left: 68px; top: 270px; width: 500px;
    font-size: 10.5px; color: var(--ink); line-height: 20.4px;
  }
  .letter-body p { margin-bottom: 7px; }
  .letter-body span { display: block; white-space: nowrap; }
  .signature {
    position: absolute; left: 427px; top: 557px;
    width: 122px; height: 40px;
    background: var(--signature-tone); border-radius: 3px;
  }
  .signatory {
    position: absolute; left: 432px; top: 593px;
    font-size: 10px; line-height: 12px; color: var(--ink-dark);
  }
  .footer-accent {
    position: absolute; left: 0; top: 737px;
    width: 17px; height: 38px; background: var(--brand-red);
  }
  .contact-list {
    position: absolute; left: 49px; top: 738px;
    list-style: none; font-size: 10px; line-height: 12px; color: var(--ink-dark);
  }
  .contact-list li { display: flex; align-items: center; gap: 3px; }
  .contact-list svg { width: 9px; height: 9px; flex: none; }
  .footer-divider {
    position: absolute; left: 163px; top: 739px;
    width: 1px; height: 34px; background: var(--rule);
  }
  .company-details {
    position: absolute; left: 186px; top: 738px;
    font-size: 10px; line-height: 12px; color: var(--ink-dark);
  }
</style>
</head>
<body>
  <main class="letterhead">
    <div class="brand-name">PIMLU</div>

    <div class="letter-date">Date, 10 September, 2020</div>

    <div class="letter-body">
      <p>
        <span>This is a sample letter that has been placed to demonstrate typing remat (Your Company). letterhead</span>
        <span>design. When positioned properly, it will serve to work in harmony with all other elements letterhead.</span>
        <span>This letterhead design is meant to project an image</span>
      </p>
      <p>
        <span>This letterhead design is meant project an image of professionalism reliability. By using simple aligen</span>
        <span>we have created a very spacious feeling. The simplicity suggest&nbsp; rengththe spaciousnes contributes h</span>
        <span>aesthetics the layout. These basic qualities along with the (Your Company)</span>
      </p>
      <p>
        <span>look and helps reinforce the (Your Company) brand. letterhead design is meant to project an image p</span>
        <span>design. When positioned properly, it will serve to work in harmony all the other elements letterhead.</span>
        <span>sionalism and reliability.</span>
      </p>
      <p>
        <span>This letterhead design is based on the (Form of your logo) form (Your Company) logo. Each stationery</span>
        <span>we have created a very spacious feeling. The simplicity suggests strength the spaciousnes contribute</span>
        <span>part of the (Form of your logo).</span>
      </p>
    </div>

    <div class="signature" role="img" aria-label="Handwritten signature of Daniel Corrow"></div>
    <div class="signatory">Daniel Corrow<br>Manager</div>

    <div class="footer-accent"></div>
    <ul class="contact-list">
      <li>
        <svg viewBox="0 0 10 10" aria-hidden="true"><circle cx="5" cy="5" r="5" fill="var(--brand-red)"/><path d="M3.3 2.6l1 1-.5.6c.3.7.8 1.2 1.5 1.5l.6-.5 1 1-.7.8C4.6 6.8 3.2 5.4 2.6 3.3z" fill="#fff"/></svg>
        02 4819 3370
      </li>
      <li>
        <svg viewBox="0 0 10 10" aria-hidden="true"><circle cx="5" cy="5" r="5" fill="var(--brand-red)"/><rect x="2.6" y="3.3" width="4.8" height="3.4" fill="#fff"/><path d="M2.6 3.3L5 5.2l2.4-1.9" fill="none" stroke="var(--brand-red)" stroke-width=".6"/></svg>
        info@pimlu.com
      </li>
      <li>
        <svg viewBox="0 0 10 10" aria-hidden="true"><circle cx="5" cy="5" r="5" fill="var(--brand-red)"/><circle cx="5" cy="5" r="2.5" fill="none" stroke="#fff" stroke-width=".7"/><path d="M2.5 5h5M5 2.5v5" stroke="#fff" stroke-width=".6"/></svg>
        www.pimlu.com
      </li>
    </ul>
    <div class="footer-divider"></div>
    <div class="company-details">
      ABN: 41 208 913 506<br>
      Lic No. 10483162<br>
      PO Box 3170, Harlow Vale NSW 2790
    </div>
  </main>
</body>
</html>
```